Professional & attention grabbing.

A business card design, front and back. I already have a logo I will attach, but I am open to something new as well.
Things to include:
Name:
Title:
Phone:
Email:
Wanting something that is professional but attention grabbing.
Also we do a lot of work using drones on natural gas pipelines (leading the future)if you want to include any of that. I'm open to ideas.
Target Market(s)
Natural gas transmission industry / greenhouse gas mitigation industry
Industry/Entity Type
Business
Colors
Designer to choose colors to be used in the design.
Look and feel
Each slider illustrates characteristics of the customer's brand and the style your logo design should communicate.

```html
<!DOCTYPE html>
<html lang="en">
<head>
<meta charset="utf-8">
<title>Kestrel Line Inspections – Business Card</title>
<link rel="stylesheet" href="https://fonts.googleapis.com/css2?family=Open+Sans:wght@400;600;700;800&display=swap">
<style>
  :root {
    --brand-red: #c41e27;
    --swoosh-grey: #5a5a5c;
    --swoosh-light: #a7a8aa;
    --ink: #4a4a4c;
    --card-white: #ffffff;
    --page-bg: #e7e5e2;
  }
  * { box-sizing: border-box; margin: 0; padding: 0; }
  html, body { width: 1200px; height: 950px; overflow: hidden; }
  body {
    background: var(--page-bg);
    font-family: "Open Sans", Arial, sans-serif;
    color: var(--ink);
    position: relative;
  }
  .card {
    position: absolute;
    left: 250px;
    width: 700px;
    height: 400px;
    border-radius: 22px;
    overflow: hidden;
    box-shadow: 0 6px 18px rgba(0,0,0,.18);
  }
  .card--front { top: 55px; background: var(--card-white); }
  .card--back { top: 495px; background: var(--brand-red); }

  .front-curves { position: absolute; inset: 0; width: 100%; height: 100%; }

  .brand-lockup {
    position: absolute;
    left: 56px;
    top: 196px;
    display: flex;
    align-items: center;
    gap: 12px;
  }
  .brand-lockup__square {
    width: 34px; height: 34px;
    background: var(--brand-red);
    flex: none;
  }
  .brand-lockup__name {
    font-weight: 700;
    font-size: 25px;
    letter-spacing: .5px;
    color: var(--swoosh-grey);
    line-height: 1.1;
    white-space: nowrap;
  }

  .divider {
    position: absolute;
    left: 340px;
    top: 160px;
    width: 1px;
    height: 150px;
    background: var(--swoosh-light);
  }

  .contact-block {
    position: absolute;
    left: 368px;
    top: 100px;
  }
  .contact-block__name {
    font-weight: 700;
    font-size: 27px;
    color: var(--brand-red);
    letter-spacing: .5px;
  }
  .contact-block__title {
    font-size: 19px;
    margin-top: 2px;
    margin-bottom: 18px;
  }
  .contact-list { list-style: none; }
  .contact-list__item {
    display: flex;
    align-items: center;
    gap: 10px;
    font-size: 18px;
    margin-bottom: 9px;
  }
  .contact-list__icon { width: 16px; height: 16px; flex: none; }

  .back-web {
    position: absolute;
    left: 22px;
    top: 200px;
    transform: rotate(-90deg);
    transform-origin: left top;
    color: var(--card-white);
    font-size: 17px;
    letter-spacing: .5px;
    white-space: nowrap;
  }
  .back-lockup {
    position: absolute;
    right: 60px;
    bottom: 60px;
    display: flex;
    align-items: center;
    gap: 14px;
  }
  .back-lockup__square {
    width: 48px; height: 48px;
    background: var(--card-white);
  }
  .back-lockup__name {
    font-weight: 700;
    font-size: 30px;
    color: var(--card-white);
    letter-spacing: .5px;
  }
</style>
</head>
<body>

<section class="card card--front" aria-label="Business card front">
  <svg class="front-curves" viewBox="0 0 700 400" preserveAspectRatio="none" aria-hidden="true">
    <path d="M0,400 V282 C150,292 320,338 470,400 Z" fill="var(--swoosh-light)"/>
    <path d="M0,400 V292 C150,302 310,346 452,400 Z" fill="var(--swoosh-grey)"/>
    <path d="M0,400 V304 C150,314 300,356 430,400 Z" fill="var(--brand-red)"/>
  </svg>

  <div class="brand-lockup">
    <span class="brand-lockup__square"></span>
    <span class="brand-lockup__name">KESTREL LINE</span>
  </div>

  <div class="divider"></div>

  <div class="contact-block">
    <p class="contact-block__name">DANIEL REYES</p>
    <p class="contact-block__title">CEO/Founder</p>
    <ul class="contact-list">
      <li class="contact-list__item">
        <svg class="contact-list__icon" viewBox="0 0 16 16" aria-hidden="true"><path d="M3,1 L6,1 L7,5 L5,6.5 C6,9 7,10 9.5,11 L11,9 L15,10 L15,13 C15,14 14,15 13,15 C6,15 1,10 1,3 C1,2 2,1 3,1 Z" fill="var(--brand-red)"/></svg>
        <span>555 014 2538</span>
      </li>
      <li class="contact-list__item">
        <svg class="contact-list__icon" viewBox="0 0 16 16" aria-hidden="true"><rect x="1" y="3" width="14" height="10" rx="1.5" fill="var(--brand-red)"/><path d="M2,4.5 L8,9 L14,4.5" stroke="#fff" stroke-width="1.4" fill="none"/></svg>
        <span>hello@kestrelline.com</span>
      </li>
      <li class="contact-list__item">
        <svg class="contact-list__icon" viewBox="0 0 16 16" aria-hidden="true"><circle cx="8" cy="8" r="7" fill="var(--brand-red)"/><ellipse cx="8" cy="8" rx="3" ry="7" fill="none" stroke="#fff" stroke-width="1"/><path d="M1,8 H15" stroke="#fff" stroke-width="1"/></svg>
        <span>www.kestrelline.com</span>
      </li>
    </ul>
  </div>
</section>

<section class="card card--back" aria-label="Business card back">
  <p class="back-web">www.kestrelline.com</p>
  <div class="back-lockup">
    <span class="back-lockup__square"></span>
    <span class="back-lockup__name">KESTREL LINE</span>
  </div>
</section>

</body>
</html>
```